Stationery for use with Ninefold Ridge reports

I would like to get a stationery design that my firm -- Ninefold Ridge Advisory -- will use as a format for reports that we send our clients. I am specifically looking for a design for use on a piece of paper or letterhead -- not business cards or envelopes.

We are an Africa based US risk intelligence and strategy firm that works with multinational corporations operating in West Africa. Our initial thinking is that we would like a color scheme consistent with our existing logo -- however we are open to other color schemes.

Also, we would like to see at least two separate versions: one with our company name and logo, the other without name and logo.

We also would like font recommendations for the stationary design.

The final design should communicate discreet professionalism and a modern approach, but it should not overshadow the words and information printed on the stationery.

Target Market(s)

Multinational corporations that currently use our products.

Font styles to use
Serif
Sans Serif

Requirements
Must have
• Sense of discreet professionalism that will not overshadow the content we put onto the stationery format.
• We would like to see designs with and without our company name/logo.
• Please suggest fonts that would work with the stationery.
Nice to have
• Ideally colors consistent with out existing logo, though we are open to and even encourage other ideas.
Should not have
• No need for business cards or envelopes.

```html
<!DOCTYPE html>
<html lang="en">
<head>
<meta charset="utf-8">
<title>Ninefold Ridge Advisory — Letterhead</title>
<link rel="stylesheet" href="https://fonts.googleapis.com/css2?family=Montserrat:wght@300;400;600;700&family=Source+Sans+3:wght@400&display=swap">
<style>
  :root {
    --navy: #233d4c;
    --gold: #b8792d;
    --gold-light: #e6ad52;
    --muted: #5f7482;
    --paper: #ffffff;
  }
  * { margin: 0; padding: 0; box-sizing: border-box; }
  html, body { width: 848px; height: 1200px; overflow: hidden; background: #fff; }
  .letterhead {
    position: relative;
    width: 848px;
    height: 1200px;
    overflow: hidden;
    color: var(--navy);
    font-family: "Source Sans 3", "Myriad Pro", sans-serif;
  }
  .frame { position: absolute; inset: 0; }
  .brand {
    position: absolute;
    top: 162px;
    left: 0;
    width: 848px;
    display: flex;
    justify-content: center;
    align-items: center;
    gap: 10px;
  }
  .brand-dot { width: 14px; height: 14px; border-radius: 50%; background: var(--gold); }
  .brand-name {
    font-family: "Montserrat", sans-serif;
    font-weight: 700;
    font-size: 20px;
    color: var(--navy);
  }
  .sender {
    position: absolute;
    top: 297px;
    left: 85px;
    font-size: 17px;
    line-height: 21px;
  }
  .sender-label {
    font-family: "Montserrat", sans-serif;
    font-weight: 600;
    font-size: 17px;
    line-height: 22px;
  }
  .headline {
    position: absolute;
    top: 389px;
    left: 85px;
    font-family: "Montserrat", sans-serif;
    font-weight: 600;
    font-size: 23.5px;
    letter-spacing: 0.2px;
  }
  .body-copy {
    position: absolute;
    top: 437px;
    left: 87px;
    width: 668px;
    font-size: 15.4px;
    line-height: 17.1px;
    letter-spacing: 0.2px;
    text-align: justify;
  }
  .body-copy p + p { margin-top: 7.5px; }
  .signoff {
    position: absolute;
    top: 873px;
    left: 87px;
    font-family: "Montserrat", sans-serif;
  }
  .signoff-name { font-size: 17px; font-weight: 400; line-height: 24px; }
  .signoff-date { font-size: 16.5px; font-weight: 300; color: var(--muted); line-height: 26px; }
  .contact {
    position: absolute;
    font-size: 12.5px;
    line-height: 15.6px;
    color: var(--navy);
  }
  .contact-web { top: 1069px; left: 200px; }
  .contact-place { top: 1093px; left: 200px; }
  .contact-mail { top: 1069px; right: 215px; text-align: right; }
  .contact-phone { top: 1093px; right: 215px; text-align: right; letter-spacing: 0.3px; }
  .icon { position: absolute; }
</style>
</head>
<body>
<main class="letterhead">
  <svg class="frame" width="848" height="1200" viewBox="0 0 848 1200" aria-hidden="true">
    <defs>
      <linearGradient id="bandGold" x1="0" x2="1" y1="0" y2="0">
        <stop offset="0" stop-color="#283f4e"/>
        <stop offset="0.2" stop-color="#b5772d"/>
        <stop offset="0.5" stop-color="#e6ad52"/>
        <stop offset="0.8" stop-color="#b5772d"/>
        <stop offset="1" stop-color="#283f4e"/>
      </linearGradient>
      <radialGradient id="ribbonTone" cx="0.5" cy="0.5" r="0.5">
        <stop offset="0" stop-color="#8a6a3e" stop-opacity="0.55"/>
        <stop offset="1" stop-color="#8a6a3e" stop-opacity="0"/>
      </radialGradient>
      <linearGradient id="paperEdge" x1="0" x2="1" y1="0" y2="0">
        <stop offset="0" stop-color="#2b4352"/>
        <stop offset="0.012" stop-color="#8fb4cc"/>
        <stop offset="0.026" stop-color="#d9eefb"/>
        <stop offset="0.045" stop-color="#ffffff"/>
        <stop offset="0.955" stop-color="#ffffff"/>
        <stop offset="0.974" stop-color="#d9eefb"/>
        <stop offset="0.988" stop-color="#8fb4cc"/>
        <stop offset="1" stop-color="#2b4352"/>
      </linearGradient>
    </defs>
    <rect class="band" width="848" height="1200" fill="url(#bandGold)"/>
    <rect class="ribbon-zone ribbon-top" x="250" y="-40" width="348" height="120" fill="url(#ribbonTone)"/>
    <rect class="ribbon-zone ribbon-bottom" x="250" y="1120" width="348" height="120" fill="url(#ribbonTone)"/>
    <path class="paper" fill="url(#paperEdge)"
      d="M0,126 C8,108 50,100 150,96 C300,90 380,80 424,68 C468,80 548,90 698,96 C798,100 840,108 848,126
         L848,1132 C840,1140 798,1145 698,1148 C548,1152 468,1155 424,1160 C380,1155 300,1152 150,1148 C50,1145 8,1140 0,1132 Z"/>
  </svg>
  <div role="img" aria-label="Decorative crossing gold ribbons at the top edge" style="position:absolute;left:250px;top:0;width:348px;height:68px"></div>
  <div role="img" aria-label="Decorative crossing gold ribbons at the bottom edge" style="position:absolute;left:250px;top:1160px;width:348px;height:40px"></div>

  <header class="brand">
    <span class="brand-dot"></span>
    <span class="brand-name">Ninefold Ridge Advisory</span>
  </header>

  <section class="sender">
    <div class="sender-label">ADDRESS</div>
    <div>48, Osu Road, Accra</div>
    <div>Ghana</div>
  </section>

  <h1 class="headline">HEADLINE</h1>

  <article class="body-copy">
    <p>Lorem ipsum dolor sit amet, consectetuer adipiscing elit, sed diam nonummy nibh euismod tincidunt ut laoreet dolore magna aliquam erat volutpat. Ut wisi enim ad minim veniam, quis nostrud exerci tation ullamcorper suscipit lobortis nisl ut aliquip ex ea commodo consequat. Duis autem vel eum iriure dolor in hendrerit in vulputate velit esse molestie consequat, vel illum dolore eu feugiat nulla facilisis at vero eros et accumsan et iusto odio dignissim qui blandit praesent luptatum zzril delenit augue duis dolore te feugait nulla facilisi.</p>
    <p>Lorem ipsum dolor sit amet, consectetuer adipiscing elit, sed diam nonummy nibh euismod tincidunt ut laoreet dolore magna aliquam erat volutpat. Ut wisi enim ad minim veniam, quis nostrud exerci tation ullamcorper suscipit lobortis nisl ut aliquip ex ea commodo consequat. Duis autem vel eum iriure dolor in hendrerit in vulputate velit esse molestie consequat, vel illum dolore eu feugiat nulla facilisis at vero eros et accumsan et iusto odio dignissim qui blandit praesent luptatum zzril delenit augue duis dolore te feugait nulla facilisi.Lorem ipsum dolor sit amet, consectetuer adipiscing elit, sed diam nonummy nibh euismod tincidunt ut laoreet dolore magna aliquam erat volutpat. Ut wisi enim ad minim veniam, quis nostrud exerci tation ullamcorper suscipit lobortis nisl ut aliquip ex ea commodo consequat. Duis autem vel eum iriure dolor in hendrerit in vulputate velit esse molestie consequat, vel illum dolore eu feugiat nulla facilisis at vero eros et accumsan et iusto odio dignissim qui blandit praesent luptatum zzril delenit augue duis dolore te feugait nulla facilisi.Lorem ipsum dolor sit amet, consectetuer adipiscing elit, sed diam nonummy nibh euismod tincidunt ut laoreet dolore magna aliquam erat volutpat. Ut wisi enim ad minim veniam, quis nostrud exerci tation ullamcorper suscipit lobortis nisl ut aliquip ex ea commodo consequat. Duis autem vel eum iriure dolor in hendrerit in vulputate velit esse molestie consequat, vel illum dolore eu feugiat nulla facilisis at vero eros et accumsan et iusto odio dignissim qui blandit praesent luptatum zzril delenit augue duis dolore te feugait nulla facilisi.</p>
  </article>

  <section class="signoff">
    <div class="signoff-name">Lorem ipsum</div>
    <div class="signoff-date">Date / Mounth / Year</div>
  </section>

  <footer>
    <svg class="icon icon-globe" style="left:172px;top:1071px" width="15" height="15" viewBox="0 0 24 24" fill="none" stroke="var(--navy)" stroke-width="1.4" aria-hidden="true">
      <circle cx="12" cy="12" r="10"/><ellipse cx="12" cy="12" rx="4.5" ry="10"/><path d="M2 12h20M4 6.5h16M4 17.5h16"/>
    </svg>
    <div class="contact contact-web">www.ridgenine.co</div>

    <svg class="icon icon-pin" style="left:171px;top:1099px" width="16" height="21" viewBox="0 0 16 21" aria-hidden="true">
      <path d="M8 0C3.6 0 0 3.5 0 7.9 0 13.5 8 21 8 21s8-7.5 8-13.1C16 3.5 12.4 0 8 0z" fill="var(--navy)"/>
      <circle cx="8" cy="7.8" r="3.1" fill="#fff"/>
    </svg>
    <div class="contact contact-place">12/4, osu road,<br>accra, ghana</div>

    <div class="contact contact-mail">desk@ridgenine.co</div>
    <svg class="icon icon-mail" style="left:663px;top:1073px" width="15" height="12" viewBox="0 0 15 12" fill="none" stroke="var(--navy)" stroke-width="1.6" aria-hidden="true">
      <rect x="1" y="1" width="13" height="10" rx="1"/><path d="M1.5 1.8 7.5 6.8 13.5 1.8"/>
    </svg>

    <div class="contact contact-phone">0302555014822<br>0302555019937</div>
    <svg class="icon icon-phone" style="left:662px;top:1101px" width="16" height="16" viewBox="0 0 24 24" fill="none" stroke="var(--navy)" stroke-width="1.6" aria-hidden="true">
      <circle cx="12" cy="12" r="10.5"/>
      <path d="M8.3 6.8c.5-.4 1.1-.3 1.4.2l1 1.7c.3.5.1 1-.3 1.3l-.6.5c.6 1.4 1.7 2.5 3.1 3.1l.5-.6c.3-.4.9-.6 1.3-.3l1.7 1c.5.3.6.9.2 1.4-.8 1-2 1.3-3.1.8-2.6-1.1-4.6-3.1-5.7-5.7-.4-1.1-.1-2.3.5-3.4z" fill="var(--navy)" stroke="none"/>
    </svg>
  </footer>
</main>
</body>
</html>
```